Brightway Haus Inc. Business Card Design

Brightway Haus Inc. is in search of a great clean design for our business cards!

Looking to incorporate our full logo and watermark on side one (however, I am open to having the text and watermark separated within the design.)

On side two, I am looking to have contact information (Name, Position, Phone #, Email, Website (www.thebrightwayhaus.ca). Can have the logo and/or watermark as part of the design if applicable.

Please add tagline "Where Shine Counts" on either side 1 or 2. This tagline can be in a sans serif, serif or cursive font as long as it compliments overall design. Capitalization can be title or sentence case depending on how it fits within the design.

Get creative!! Looking for a clean, crisp, premium design! Looking for a glossy card finish with spot UV features when printed. Cards will also be printed with rounded corners. Standard dimensions (3.5 x 2).

Target Market(s)

B2B - primary clients are business owners or property management corporations. (residential jobs are few and far between)

Industry/Entity Type

Business

Contact Information for Business Card

- clean, crisp design
- double sided
- spot UV accents and glossy finish upon printing
- standard business card size (3.5 x 2) with rounded corners
- please see project description for requirements per side

Font styles to use
Sans Serif

Requirements
Must have
• - adequate bleeds with print ready files
• - cohesive design elements between side 1 & 2
• - spot UV elements (can be on both sides or just one, use your discretion)
• - colour pallet should match the logo file provided
• - incorporate tagline "where shine counts" (this tagline can be in a serif or sans serif font as long as it is complimentary to the overall design.
Nice to have
• - Premium elements with a clean design
Should not have
• - Please omit cartoon or whimsical like designs, think premium.
• - Colours should not stray from the pallet of the provided logo.

```html
<!DOCTYPE html>
<html lang="en">
<head>
<meta charset="utf-8">
<title>Brightway Haus Inc. Business Cards</title>
<link href="https://fonts.googleapis.com/css2?family=Roboto:wght@400;500;700;900&display=swap" rel="stylesheet">
<style>
  :root {
    --backdrop: #2e2a28;
    --card: #17191c;
    --card-edge: #22252a;
    --teal: #2bbfc0;
    --navy: #1f2f6b;
    --white: #f2f3f4;
    --silver: #c9cbce;
    --silver-dim: #7d8084;
  }
  * { margin: 0; padding: 0; box-sizing: border-box; }
  html, body {
    width: 1200px; height: 769px; overflow: hidden;
    background: var(--backdrop);
    font-family: "Roboto", Arial, sans-serif;
  }
  .canvas {
    position: relative; width: 1200px; height: 769px;
    background: radial-gradient(ellipse at 50% 40%, #3a3431 0%, var(--backdrop) 70%);
  }
  .card {
    position: absolute; top: 236px;
    width: 525px; height: 300px;
    background: var(--card);
    border-radius: 12px;
    box-shadow: 0 18px 40px rgba(0,0,0,.55), inset 0 0 0 1px var(--card-edge);
    overflow: hidden;
  }
  .card--contact { left: 50px; }
  .card--brand { left: 625px; }

  /* contact side */
  .accent-bar {
    position: absolute; left: 24px; top: 62px;
    width: 8px; height: 30px; background: var(--teal);
  }
  .person { position: absolute; left: 48px; top: 54px; }
  .person__name { color: var(--teal); font-weight: 500; font-size: 19px; letter-spacing: .3px; }
  .person__role { color: var(--navy); font-weight: 500; font-size: 13px; letter-spacing: .6px; margin-top: 2px; }
  .address {
    position: absolute; left: 48px; top: 150px;
    color: var(--white); font-size: 12.5px; line-height: 16px;
  }
  .contact-list {
    position: absolute; left: 48px; top: 192px;
    list-style: none; color: var(--white); font-size: 12.5px;
  }
  .contact-list li { display: flex; align-items: center; height: 17px; }
  .contact-list svg { width: 11px; height: 11px; margin-right: 9px; fill: var(--teal); flex: none; }
  .mark-block {
    position: absolute; left: 350px; top: 82px;
    display: flex; flex-direction: column; align-items: center; gap: 10px;
  }
  .mark-block__square { width: 110px; height: 110px; background: var(--teal); box-shadow: 10px 10px 0 var(--navy); }
  .mark-block__name { color: var(--white); font-size: 12.5px; font-weight: 500; letter-spacing: .4px; margin-top: 6px; }

  /* brand side */
  .brand {
    position: absolute; left: 0; right: 0; top: 108px;
    display: flex; justify-content: center; align-items: center; gap: 12px;
  }
  .brand__square { width: 34px; height: 34px; background: var(--silver); }
  .brand__name { color: var(--silver); font-weight: 900; font-size: 34px; letter-spacing: .5px; line-height: 1; }
  .tagline {
    position: absolute; left: 60px; right: 60px; top: 170px;
    display: flex; align-items: center; gap: 10px;
    color: var(--white); font-size: 14px;
  }
  .tagline::before, .tagline::after {
    content: ""; flex: 1; height: 1px;
    background: linear-gradient(90deg, transparent, var(--silver-dim));
  }
  .tagline::after { background: linear-gradient(90deg, var(--silver-dim), transparent); }
</style>
</head>
<body>
<main class="canvas">
  <section class="card card--contact" aria-label="Contact side">
    <div class="accent-bar"></div>
    <div class="person">
      <p class="person__name">DANIEL REYES</p>
      <p class="person__role">CEO/FOUNDER</p>
    </div>
    <p class="address">4120 Harbourview Drive<br>Halifax, Nova Scotia B3H 2Y9</p>
    <ul class="contact-list">
      <li><svg viewBox="0 0 24 24"><path d="M6.6 10.8a15 15 0 0 0 6.6 6.6l2.2-2.2c.3-.3.7-.4 1-.2 1.1.4 2.3.6 3.6.6.6 0 1 .4 1 1V20c0 .6-.4 1-1 1A17 17 0 0 1 3 4c0-.6.4-1 1-1h3.5c.6 0 1 .4 1 1 0 1.3.2 2.5.6 3.6.1.3 0 .7-.2 1z"/></svg>902 555 0148</li>
      <li><svg viewBox="0 0 24 24"><path d="M7 1h10a2 2 0 0 1 2 2v18a2 2 0 0 1-2 2H7a2 2 0 0 1-2-2V3a2 2 0 0 1 2-2zm0 3v14h10V4z"/></svg>902 555 0172</li>
      <li><svg viewBox="0 0 24 24"><path d="M6 2h12v6H6zM3 9h18a2 2 0 0 1 2 2v7h-4v4H5v-4H1v-7a2 2 0 0 1 2-2zm4 7v4h10v-4z"/></svg>902 555 0193</li>
      <li><svg viewBox="0 0 24 24"><path d="M2 4h20v16H2zm2 2v.5l8 5 8-5V6z"/></svg>daniel@brightwayhaus.ca</li>
      <li><svg viewBox="0 0 24 24"><circle cx="12" cy="12" r="10"/></svg>www.thebrightwayhaus.ca</li>
    </ul>
    <div class="mark-block">
      <div class="mark-block__square"></div>
      <p class="mark-block__name">Brightway Haus Inc.</p>
    </div>
  </section>

  <section class="card card--brand" aria-label="Brand side">
    <div class="brand">
      <div class="brand__square"></div>
      <p class="brand__name">BRIGHTWAY HAUS INC.</p>
    </div>
    <p class="tagline">Where Shine Counts</p>
  </section>
</main>
</body>
</html>
```